Wedding filmmaker needs artistic business card design - brightwaterreels.ca

We are high end wedding filmmakers in a major market who produce cinematic wedding films. We require a business card design that communicates our quality, artistry, and professionalism yet looks progressive and friendly. Colors and design should skew appeal more to the bride-to-be who is usually the decision maker but not be overtly feminine per se. This means generally light pastel shades of ivory, purple, pink, yellow, as examples.
We already have a name logo established: the words "Brightwater Reels" in the font Great Vibes. Designs must use Kraft natural cardstock as the print stock and am leaning heavily toward our name logo in white, but I am open to black as well. Please design any color elements with spot white underneath where possible.
Do not try to compliment or take inspiration from our website design. Treat the card design as a separate stand alone.
Thank you so much for your hard work!

Target Market(s)

Affluent couples spending $50,000+ on their wedding

Industry/Entity Type

Progressive

Contact Information for Business Card

Peter Brightwater
Producer
905-482-7139
www.brightwaterreels.ca
peter@brightwaterreels.ca
twitter @brightwater287

Font styles to use
Serif
Sans Serif

Requirements
Must have
• - Brightwater Reels name logo (reference GIF uploaded for reference only) and catch phrase: Breathtaking wedding films (I'm open to capitalizing all three words, or just first, or all in small caps). I favor logo, and catch phrase on front of card and my contact details on the other side but if you feel strongly about a different design, go for it!
• - Design must be submitted shown on Kraft natural cardstock NOT WHITE cardstock, If you're not familiar with Kraft, this is what it looks like: http://www.quillandlatchjournal.com/wp-content/uploads/2013/07/il_570xN.382745196_kq3m.jpg
Nice to have
• - An original graphic element (eg. movie reel, bouquet, confetti, etc.) that compliments the name logo but is subtle and discreet, doesn't overpower or entangle it.
• -Great use of balance, composition, negative space, etc. I like clean tasteful design
Should not have
• -Lousy boring clip art.
• -Graphic elements, fonts, or color palette from our website
• -White cardstock background
• -designs you have previously submitted for other contests
• -Bold dark colors (eg. red, orange navy blue, etc.)
• -High tech futuristic designs like you'd create for a software company

```html
<!DOCTYPE html>
<html lang="en">
<head>
<meta charset="utf-8">
<title>Brightwater Reels – Business Card</title>
<link href="https://fonts.googleapis.com/css2?family=Great+Vibes&family=Josefin+Sans:wght@400;600&display=swap" rel="stylesheet">
<style>
  :root {
    --backdrop: #f4f0e8;
    --kraft: #c9a77c;
    --kraft-shade: #b8946a;
    --lavender: #cbbbdc;
    --blush: #f0d3da;
    --ivory: #fffdf6;
    --ink: #4e3b2a;
    --ink-soft: #6b553f;
  }
  * { box-sizing: border-box; margin: 0; padding: 0; }
  html, body { width: 1200px; height: 900px; overflow: hidden; }
  body {
    background: var(--backdrop);
    display: flex;
    flex-direction: column;
    align-items: center;
    justify-content: center;
    gap: 60px;
    font-family: "Josefin Sans", sans-serif;
  }
  .card {
    position: relative;
    width: 560px;
    height: 340px;
    border-radius: 34px;
    background: linear-gradient(160deg, var(--kraft) 35%, var(--kraft-shade));
    box-shadow: 0 10px 24px rgba(60,40,20,0.18);
    overflow: hidden;
  }
  .card__swoosh { position: absolute; inset: 0; }
  .wordmark {
    font-family: "Great Vibes", cursive;
    color: var(--ivory);
    font-weight: 400;
    line-height: 1;
  }
  .card--front .wordmark {
    position: absolute;
    top: 42px;
    left: 160px;
    font-size: 52px;
  }
  .contact-owner {
    position: absolute;
    top: 150px;
    left: 150px;
    width: 160px;
    text-align: right;
    font-size: 10.5px;
    letter-spacing: 1.4px;
    text-transform: uppercase;
    color: var(--ink-soft);
    line-height: 1.65;
  }
  .contact-owner__name { color: var(--ink); font-weight: 600; font-size: 12px; letter-spacing: 2.2px; }
  .contact-owner__address { margin-top: 12px; }
  .divider {
    position: absolute;
    top: 150px;
    left: 322px;
    width: 1px;
    height: 104px;
    background: var(--ink-soft);
    opacity: 0.6;
  }
  .contact-list {
    position: absolute;
    top: 150px;
    left: 334px;
    list-style: none;
    font-size: 10px;
    letter-spacing: 1px;
    text-transform: uppercase;
    color: var(--ink-soft);
    line-height: 21px;
  }
  .contact-list li { display: flex; align-items: center; gap: 6px; }
  .contact-list svg { width: 12px; height: 12px; flex: none; }
  .card--back {
    display: flex;
    flex-direction: column;
    align-items: center;
    justify-content: center;
    gap: 18px;
  }
  .card--back .wordmark { font-size: 74px; }
  .tagline {
    font-size: 13px;
    letter-spacing: 4px;
    text-transform: uppercase;
    color: var(--ink);
  }
</style>
</head>
<body>

  <section class="card card--front" aria-label="Card front with contact details">
    <svg class="card__swoosh" viewBox="0 0 560 340" aria-hidden="true">
      <path d="M0 0 H110 C35 45 12 150 75 228 C130 292 250 322 380 340 H0 Z" fill="var(--lavender)"/>
      <path d="M86 0 C18 55 2 160 64 238 C115 298 215 326 300 340" fill="none" stroke="var(--ivory)" stroke-width="8"/>
      <path d="M126 0 C62 50 48 150 108 222 C150 270 215 298 300 310" fill="none" stroke="var(--blush)" stroke-width="2.5"/>
    </svg>

    <h1 class="wordmark">Brightwater Reels</h1>

    <div class="contact-owner">
      <p class="contact-owner__name">Mark Dalton</p>
      <p class="contact-owner__role">Owner / C.E.O</p>
      <p class="contact-owner__address">Suite # 418, Elm Bldg,<br>NY 40712</p>
    </div>

    <div class="divider"></div>

    <ul class="contact-list">
      <li><svg viewBox="0 0 12 12"><circle cx="6" cy="6" r="6" fill="var(--ivory)"/><path d="M4 3.2 l1.2 1.3 -0.6 0.8 q0.8 1.4 2 2 l0.8 -0.6 1.3 1.2 -0.8 1 q-3.2 -0.6 -4.4 -4.4z" fill="var(--ink)"/></svg>905-482-7139</li>
      <li><svg viewBox="0 0 12 12"><circle cx="6" cy="6" r="6" fill="var(--ivory)"/><rect x="4" y="2.8" width="4" height="6.4" rx="0.8" fill="var(--ink)"/></svg>905-482-7140</li>
      <li><svg viewBox="0 0 12 12"><circle cx="6" cy="6" r="6" fill="var(--ivory)"/><rect x="3" y="4" width="6" height="4.5" fill="var(--ink)"/></svg>905-482-7141</li>
      <li><svg viewBox="0 0 12 12"><circle cx="6" cy="6" r="6" fill="var(--ivory)"/><rect x="3" y="3.8" width="6" height="4.4" fill="none" stroke="var(--ink)"/><path d="M3 4 L6 6.3 L9 4" fill="none" stroke="var(--ink)" stroke-width="0.9"/></svg>mail@placeholdersite.com</li>
      <li><svg viewBox="0 0 12 12"><circle cx="6" cy="6" r="6" fill="var(--ivory)"/><circle cx="6" cy="6" r="3" fill="none" stroke="var(--ink)"/><path d="M3 6 H9" stroke="var(--ink)" stroke-width="0.8"/></svg>www.placeholdersite.com</li>
    </ul>
  </section>

  <section class="card card--back" aria-label="Card back with name logo and tagline">
    <p class="wordmark">Brightwater Reels</p>
    <p class="tagline">Breathtaking Wedding Films</p>
  </section>

</body>
</html>
```